Business Card Design Project

We are not a new company, but renamed to "Vantorin Kitchens" last year. We specialize in modern high-end cabinetry imports. We would like to communicate a sense of quality and cutting edge technology. Ideally the design would incorporate our logo colors, silver, red and preferably a black, matte background. Though we are open to suggestions.
Logo is attached.
Edit: I have attached rough drafts of the previous cards, this way you will have all necessary content that needs to go on the cards.
Updates
Project Deadline Extended
Reason: We have received a lot of great designs, but due to the sheer number we couldn't respond to all. We will extend the deadline for another 7 days to finalize and provide feedback to designers.
Thank you for your hard work!
Industry/Entity Type
Business
Look and feel
Each slider illustrates characteristics of the customer's brand and the style your logo design should communicate.

```html
<!DOCTYPE html>
<html lang="en">
<head>
<meta charset="utf-8">
<title>Vantorin Kitchens – Business Card</title>
<link rel="stylesheet" href="https://fonts.googleapis.com/css2?family=Arimo:wght@400;700&display=swap">
<style>
  :root {
    --backdrop: #c8d3d1;
    --card-black: #0b0b0b;
    --card-sheen: #2e2e2e;
    --silver: #c4c4c4;
    --silver-line: #8a8a8a;
    --red: #e0151f;
    --white: #f2f2f2;
  }
  * { margin: 0; padding: 0; box-sizing: border-box; }
  html, body {
    width: 1200px; height: 973px; overflow: hidden;
    background: var(--backdrop);
    font-family: "Arimo", Arial, sans-serif;
  }
  .canvas {
    width: 1200px; height: 973px;
    display: flex; flex-direction: column;
    align-items: center; justify-content: center; gap: 64px;
  }
  .card {
    position: relative;
    width: 620px; height: 354px;
    background:
      radial-gradient(ellipse 70% 60% at 55% 45%, var(--card-sheen) 0%, var(--card-black) 75%);
    box-shadow: 0 6px 18px rgba(0,0,0,0.18);
    overflow: hidden;
  }
  .card--back { border-left: 4px solid var(--red); }

  .brand-name {
    font-family: "Arimo", Arial, sans-serif;
    font-weight: 700;
    color: var(--silver);
    text-transform: uppercase;
    letter-spacing: 2px;
    white-space: nowrap;
  }
  .brand-mark {
    display: inline-block;
    background: var(--silver);
    vertical-align: middle;
  }

  /* Back: contact side */
  .card--back .brand {
    position: absolute; left: 28px; top: 150px;
    display: flex; align-items: center; gap: 12px;
  }
  .card--back .brand .brand-mark { width: 22px; height: 22px; }
  .card--back .brand .brand-name { font-size: 25px; }
  .divider {
    position: absolute; left: 0; top: 205px;
    width: 330px; height: 1px; background: var(--silver-line);
  }
  .divider--name {
    left: 330px; top: 58px; width: 0;
  }
  .contact {
    position: absolute; right: 28px; top: 40px;
    text-align: right; color: var(--white);
  }
  .contact__name {
    font-weight: 700; font-size: 15px; letter-spacing: 0.5px;
    padding-left: 60px;
    border-top: 1px solid var(--silver-line);
    padding-top: 4px;
  }
  .contact__title { color: var(--red); font-size: 13px; margin-bottom: 8px; }
  .contact__list { list-style: none; font-size: 13px; line-height: 19px; }
  .contact__list li { display: flex; justify-content: flex-end; align-items: center; gap: 6px; }
  .icon { width: 11px; height: 11px; fill: var(--red); flex: none; }
  .contact__email {
    position: absolute; right: 28px; top: 228px;
    color: var(--white); font-size: 13px;
    display: flex; align-items: center; gap: 6px;
  }
  .contact__address {
    position: absolute; right: 28px; top: 270px;
    color: var(--white); font-size: 13px;
  }

  /* Front: brand side */
  .card--front .brand {
    position: absolute; inset: 0;
    display: flex; align-items: center; justify-content: center; gap: 16px;
  }
  .card--front .brand .brand-mark { width: 34px; height: 34px; }
  .card--front .brand .brand-name { font-size: 38px; }
</style>
</head>
<body>
<main class="canvas">

  <section class="card card--back">
    <div class="brand">
      <span class="brand-mark"></span>
      <span class="brand-name">Vantorin Kitchens</span>
    </div>
    <div class="divider"></div>

    <div class="contact">
      <p class="contact__name">MARCUS DELANY</p>
      <p class="contact__title">Director</p>
      <ul class="contact__list">
        <li>
          <svg class="icon" viewBox="0 0 12 12" aria-hidden="true"><path d="M2.5 1h2l1 3-1.3 1a6 6 0 0 0 2.8 2.8l1-1.3 3 1v2c0 .6-.4 1-1 1A10 10 0 0 1 1.5 2c0-.6.4-1 1-1z"/></svg>
          555.210.4871
        </li>
        <li>
          <svg class="icon" viewBox="0 0 12 12" aria-hidden="true"><path d="M3 1h6v3H3zM1 5h10v4H9v2H3V9H1zM4 8v2h4V8z"/></svg>
          555.210.4872
        </li>
        <li>
          <svg class="icon" viewBox="0 0 12 12" aria-hidden="true"><path d="M3.5 0h5c.6 0 1 .4 1 1v10c0 .6-.4 1-1 1h-5c-.6 0-1-.4-1-1V1c0-.6.4-1 1-1zM4 2v7h4V2z"/></svg>
          555.318.6640
        </li>
      </ul>
    </div>

    <p class="contact__email">
      <svg class="icon" viewBox="0 0 12 12" aria-hidden="true"><path d="M1 2.5h10v7H1zM1.6 3l4.4 3.5L10.4 3z"/></svg>
      marcus@vantorinkitchens.ca
    </p>
    <p class="contact__address">1820 - 47 Ave. Lakeview, AB T9X 2K4 &nbsp;·&nbsp; vantorinkitchens.ca</p>
  </section>

  <section class="card card--front">
    <div class="brand">
      <span class="brand-mark"></span>
      <span class="brand-name">Vantorin Kitchens</span>
    </div>
  </section>

</main>
</body>
</html>
```